Letter design, envelope design, and more

Hello, we the Tavrin Gmbh are looking for our shop. Letter C5. Design does not have to be like a business card, so it can have straight lines. Only the color is important. The logo is the text under TaVRin omit.It should not be playful but Profesionel

Font styles to use
Sans Serif

Colors
0555a3
3176b5
85abd2
85cae6
34a7d8
0792cd
cee9f5
cfdfed
000000

Requirements
Must have
• Color like business card, Please, with the text under TaVRin, Correct address Lindmattstr. 4 Zip code 9517 Rietwil, as well as Couvert Without addressing only design and logo with TaVrn
Nice to have
• more writing articles
Should not have
• Not too colored, Text under TaVRin, bright colors

```html
<!DOCTYPE html>
<html lang="en">
<head>
<meta charset="utf-8">
<title>Tavrin Gmbh – Letterhead and Envelope</title>
<link href="https://fonts.googleapis.com/css2?family=Lato:ital,wght@0,400;0,700;0,900;1,400&family=Kaushan+Script&display=swap" rel="stylesheet">
<style>
  :root {
    --navy: #25266b;
    --steel: #7f9db8;
    --rule: #8ea6bf;
    --ink: #4a4a50;
    --stage: #c8c9cb;
    --paper: #ffffff;
    --paper-shade: #e3e4e7;
  }
  * { box-sizing: border-box; margin: 0; padding: 0; }
  html, body { width: 1200px; height: 703px; overflow: hidden; }
  body {
    background: var(--stage);
    font-family: "Lato", Arial, sans-serif;
    position: relative;
  }

  /* Letterhead */
  .letter {
    position: absolute; left: 52px; top: 56px;
    width: 428px; height: 602px;
    background: linear-gradient(170deg, var(--paper) 0%, var(--paper) 25%, var(--paper-shade) 100%);
    box-shadow: 0 0 1px rgba(0,0,0,.25);
  }
  .brand {
    position: absolute;
    display: flex; align-items: center; gap: 8px;
  }
  .brand-mark { background: var(--navy); }
  .brand-name {
    font-weight: 900; color: var(--navy); letter-spacing: .5px; line-height: 1;
  }
  .letter .brand { left: 24px; top: 18px; }
  .letter .brand-mark { width: 34px; height: 34px; }
  .letter .brand-name { font-size: 28px; }

  .rule-line { position: absolute; height: 1.5px; background: var(--rule); }
  .web {
    position: absolute; font-size: 10.5px; letter-spacing: 2px; color: var(--ink);
  }
  .web b { font-weight: 400; color: var(--steel); }
  .letter .rule-left { left: 0; top: 68px; width: 298px; }
  .letter .rule-right { left: 410px; top: 68px; width: 18px; }
  .letter .web { left: 307px; top: 62px; }

  .letter-body { position: absolute; left: 24px; top: 99px; width: 385px; color: var(--ink); }
  .letter-body p { font-size: 8.4px; line-height: 12.9px; margin-bottom: 10.5px; }
  .letter-body .salutation {
    font-size: 11px; line-height: 14px; font-weight: 700; color: var(--navy); margin-bottom: 6px;
  }
  .letter-body .closing { font-size: 12.5px; line-height: 15px; margin: 19px 0 0; color: var(--ink); }
  .letter-body .signature {
    font-family: "Kaushan Script", cursive; font-size: 21px; line-height: 26px;
    color: var(--navy); margin: 2px 0 0;
  }

  .contact {
    position: absolute; left: 0; right: 0; top: 583px;
    display: flex; justify-content: center; align-items: center;
    font-size: 8px; color: var(--ink);
  }
  .contact-item { display: flex; align-items: center; gap: 3px; padding: 0 11px; }
  .contact-item + .contact-item { border-left: 1px solid #b9bcc4; }
  .contact-item svg { width: 8px; height: 8px; }

  /* Envelope */
  .envelope { position: absolute; left: 534px; top: 90px; width: 603px; height: 534px; }
  .flap { position: absolute; left: 0; top: 0; width: 603px; height: 106px; }
  .envelope-face {
    position: absolute; left: 0; top: 105px; width: 603px; height: 429px;
    background: var(--paper); box-shadow: 0 0 1px rgba(0,0,0,.25);
  }
  .envelope .brand { left: 30px; top: 133px; }
  .envelope .brand-mark { width: 38px; height: 38px; }
  .envelope .brand-name { font-size: 31px; }
  .envelope .rule-left { left: 0; top: 512px; width: 240px; }
  .envelope .rule-right { left: 362px; top: 512px; width: 241px; }
  .envelope .web { left: 250px; top: 505px; }
</style>
</head>
<body>

<section class="letter" aria-label="Letterhead">
  <div class="brand">
    <span class="brand-mark"></span>
    <span class="brand-name">TaVRin</span>
  </div>
  <span class="rule-line rule-left"></span>
  <span class="web">www.<b>tavrin</b>.ch</span>
  <span class="rule-line rule-right"></span>

  <div class="letter-body">
    <p class="salutation">Dear Mr. Lorem,</p>
    <p>Lorem ipsum dolor sit amet, consectetuer adipiscing elit, sed diam nonummy nibh euismod tincidunt ut laoreet dolore magna aliquam erat volutpat. Ut wisi enim ad minim veniam, quis nostrud exerci tation ullamcorper suscipit lobortis nisl ut aliquip ex ea commodo consequat. Duis autem vel eum iriure dolor in hendiusto odio dignissim qui blandit praesent luptatum zzril delenit.facilisi.</p>
    <p>Lorem ipsum dolor sit amet, consectetuer adipiscing elit, sed diam nonummy nibh euismod tincidunt ut laoreet dolore magna aliquam erat volutpat. Ut wisi enim ad minim veniam, quis nostrud exerci tation ullamcorper suscipit lobortis nisl ut aliquip ex ea commodo consequat.</p>
    <p>Lorem ipsum dolor sit amet, consectetuer adipiscing elit, sed diam nonummy nibh euismod tincidunt ut laoreet dolore magna aliquam erat volutpat. Ut wisi enim ad minim veniam, quis nostrud exerci tation ullamcorper suscipit lobortis nisl ut aliquip ex ea commodo consequat. Duis autem vel eum iriure dolor in hendiusto odio dignissim qui blandit praesent luptatum zzril delenit.facilisi.</p>
    <p>Lorem ipsum dolor sit amet, consectetuer adipiscing elit, sed diam nonummy nibh euismod tincidunt ut laoreet dolore magna aliquam erat volutpat. Ut wisi enim ad minim veniam, quis nostrud exerci tation ullamcorper suscipit lobortis nisl ut aliquip ex ea commodo consequat.</p>
    <p>Lorem ipsum dolor sit amet, consectetuer adipiscing elit, sed diam nonummy nibh euismod tincidunt ut laoreet dolore magna aliquam erat volutpat. Ut wisi enim ad minim veniam, quis nostrud exerci tation ullamcorper suscipit lobortis nisl ut aliquip ex ea commodo consequat. Duis autem vel eum iriure dolor in hendiusto odio dignissim qui blandit praesent luptatum zzril delenit.facilisi.</p>
    <p>Lorem ipsum dolor sit amet, consectetuer adipiscing elit, sed diam nonummy nibh euismod tincidunt ut laoreet dolore magna aliquam erat volutpat. Ut wisi enim ad minim veniam, quis nostrud exerci tation ullamcorper suscipit lobortis nisl ut aliquip ex ea commodo consequat.</p>
    <p class="closing">Sincerely Your,</p>
    <p class="signature">Your Name</p>
  </div>

  <div class="contact">
    <span class="contact-item">
      <svg viewBox="0 0 10 10" aria-hidden="true"><circle cx="5" cy="5" r="4.3" fill="none" stroke="#25266b" stroke-width="1"/><path d="M5 2.4a1.7 1.7 0 0 1 1.7 1.7C6.7 5.4 5 7.6 5 7.6S3.3 5.4 3.3 4.1A1.7 1.7 0 0 1 5 2.4z" fill="#25266b"/></svg>
      Lindmattstr. 4, 9517 Rietwil
    </span>
    <span class="contact-item">
      <svg viewBox="0 0 10 10" aria-hidden="true"><circle cx="5" cy="5" r="4.3" fill="none" stroke="#25266b" stroke-width="1"/><path d="M3.4 2.6l1 1-.6.7c.3.7.8 1.2 1.5 1.5l.7-.6 1 1-.8.9C4.6 6.9 3.1 5.4 2.9 3.4z" fill="#25266b"/></svg>
      +41 71 555 20 40
    </span>
    <span class="contact-item">
      <svg viewBox="0 0 10 10" aria-hidden="true"><rect x="1" y="2.5" width="8" height="5.5" fill="#25266b"/><path d="M1 2.5l4 3 4-3" fill="none" stroke="#fff" stroke-width=".8"/></svg>
      info@tavrin.ch
    </span>
  </div>
</section>

<section class="envelope" aria-label="C5 envelope">
  <svg class="flap" viewBox="0 0 603 106" aria-hidden="true">
    <path d="M0 106 L10 70 Q16 56 36 52 L276 3 Q292 -1 308 3 L568 56 Q588 60 592 74 L603 106 Z" fill="#25266b"/>
  </svg>
  <div class="envelope-face"></div>
  <div class="brand">
    <span class="brand-mark"></span>
    <span class="brand-name">TaVRin</span>
  </div>
  <span class="rule-line rule-left"></span>
  <span class="web">www.<b>tavrin</b>.ch</span>
  <span class="rule-line rule-right"></span>
</section>

</body>
</html>
```